Company posters for office wall

We are looking for 3 posters with same look and feel for company walls in each location.
1. Singapore - With Voriant Asia
2. Barcelona - With Voriant Europe
3. Cape Town - With Voriant Africa

The poster can either be like a company branding poster similar to examples included or like a movie poster also includes. We have added a number of picture that can be used but happy to add more or even you add your own graphics

Looking to incorporate company logo, pictures with the design. Have added examples from Chirpline site so there is some link to this branding

Poster size will be A1 for each poster

Reason: We are looking for really good quality designs and have just updated the specifications

Target Market(s)

Internal company we are fintech

Industry/Entity Type

It Company

Colors
ffffff

Requirements
Must have
• seperate poster for each location
• - With Voriant Africa, Europe and Asia under each
• - Can provide company contact location details which should be added to each poster
• - we are looking for clean design so using the pictures but not too busy should be 'fashion' industry type poster like for a high class brand
• Voriant Europe
• Carrer de Tuset 517, 04-01
• 08021 Barcelona
• Spain
• Voriant Singapore
• 9th Floor, 48 Keppel Way, 049317
• Singapore
• Voriant Africa
• Harbour Court, 7 Upper Wale Rd, Cape Town, 8002, South Africa
Nice to have
• We have included a range of pictures that can be added into the design for each country / region

```html
<!DOCTYPE html>
<html lang="en">
<head>
<meta charset="utf-8">
<title>Voriant Singapore – Office Poster</title>
<link rel="stylesheet" href="https://fonts.googleapis.com/css2?family=Josefin+Sans:wght@300;400;600&display=swap">
<style>
  :root {
    --paper: #ffffff;
    --ink: #1c1c1c;
    --accent-red: #e4002b;
    --map-grey: #e6e6e6;
    --sky-top: #1f4fa0;
    --sky-mid: #6f8fc4;
    --sky-dusk: #e9c7a8;
    --water: #dfe5ef;
  }
  * { margin: 0; padding: 0; box-sizing: border-box; }
  html, body { width: 849px; height: 1200px; overflow: hidden; background: var(--paper); }
  .poster {
    position: relative;
    width: 849px;
    height: 1200px;
    overflow: hidden;
    background: var(--paper);
    font-family: "Josefin Sans", sans-serif;
    color: var(--ink);
  }
  .skyline-photo {
    position: absolute;
    left: 0; top: 0;
    width: 849px; height: 470px;
    background: linear-gradient(to bottom,
      var(--sky-top) 0%,
      var(--sky-mid) 25%,
      var(--sky-dusk) 48%,
      var(--water) 66%,
      var(--paper) 100%);
  }
  .island-map {
    position: absolute;
    left: 0; top: 770px;
    width: 849px; height: 430px;
    background: linear-gradient(to bottom, var(--map-grey), #ededed);
    clip-path: polygon(0 28%, 18% 14%, 34% 4%, 46% 0, 58% 16%, 70% 14%, 84% 10%, 100% 8%, 100% 100%, 0 100%);
  }
  .connectivity-illustration {
    position: absolute;
    left: 228px; top: 372px;
    width: 394px; height: 530px;
    border-radius: 46% 46% 12% 12%;
    background:
      radial-gradient(circle at 48% 10%, rgba(228,74,130,.55), transparent 30%),
      radial-gradient(circle at 20% 30%, rgba(22,160,180,.5), transparent 30%),
      radial-gradient(circle at 85% 30%, rgba(240,130,50,.5), transparent 30%),
      radial-gradient(circle at 15% 52%, rgba(120,190,60,.5), transparent 28%),
      radial-gradient(circle at 88% 50%, rgba(245,195,60,.5), transparent 28%),
      linear-gradient(to bottom, rgba(170,90,200,.25), rgba(255,255,255,0) 95%);
  }
  .brand {
    position: absolute;
    left: 0; top: 950px;
    width: 849px;
    text-align: center;
  }
  .brand-name {
    display: block;
    font-weight: 400;
    font-size: 84px;
    line-height: 1;
    letter-spacing: 1px;
    color: var(--ink);
  }
  .brand-region {
    display: block;
    margin-top: 8px;
    font-weight: 400;
    font-size: 20px;
    letter-spacing: 3px;
    color: var(--ink);
  }
  .address {
    position: absolute;
    left: 0; top: 1088px;
    width: 849px;
    text-align: center;
    font-weight: 400;
    font-size: 26px;
    letter-spacing: 1px;
    color: var(--ink);
  }
  .address-city {
    position: absolute;
    left: 180px; top: 1120px;
    width: 488px;
    display: flex;
    align-items: center;
    gap: 10px;
    font-weight: 400;
    font-size: 24px;
    letter-spacing: 1px;
    color: var(--ink);
  }
  .address-city .rule {
    flex: 1;
    height: 2px;
    background: var(--accent-red);
  }
</style>
</head>
<body>
  <main class="poster">
    <div class="skyline-photo" role="img" aria-label="Photograph of the Singapore waterfront skyline at dusk with the observation wheel, fading into white"></div>
    <div class="island-map" role="img" aria-label="Pale grey map outline of Singapore island"></div>
    <div class="connectivity-illustration" role="img" aria-label="Colourful illustration of connected app icons rising like a tree from the map"></div>

    <div class="brand">
      <span class="brand-name">Voriant</span>
      <span class="brand-region">SINGAPORE</span>
    </div>

    <p class="address">9TH FLOOR, 48 KEPPEL WAY, 049317</p>
    <p class="address-city"><span class="rule"></span>SINGAPORE<span class="rule"></span></p>
  </main>
</body>
</html>
```